2 sided postcard for New Internet Customers

We would like a design for a two sided postcard (with room for mailing label), dimensions 9 1/4 by 6 1/4 to be sent via US Mail.

The postcard needs to include our logo (attached) and the text
Fiber Optic Internet
555-318-2094
http://www.brightmesh.example
Speeds up to 1 Gig, with packages starting at $55

These will be sent to people who do not have our service.

Since this is going to be "junk mail" we probably only have 1 second or less to capture someone's attention to encourage them to read the entire postcard.

We are a "mom and pop" telecommunications company that provides internet, phone, and television services on the fiber optic network that we designed, built, and maintain.

We started as a dial up ISP in 1995, and have extraordinary technical support based in Freeport PA, our customers actually get the speeds they pay for, and our service is highly reliable.

We have a slogan (which you can choose to use or ignore) which is
"I Got Zoomed with Pellworth"

Existing customers can earn a $50 credit for every new customer they refer to us. Unlike most large cable and internet companies we have very happy customers... some who have stayed with us for decades.

I've attached our previous postcard, which I really dislike. It does have a blank spot for where the mailing label should go.

Target Market(s)

New Internet Customers in Western Pennsylvania

Industry/Entity Type

Internet

Font styles to use
Other font styles liked:
• Just match our logo.

Colors

Designer to choose colors to be used in the design.

Requirements
Must have
• The postcard needs to include our logo, and the text Fiber Optic Internet 555-318-2094 http://www.brightmesh.example Speeds up to 1 Gig, with packages starting at $55
Nice to have
• The colors and fonts should look good with our logo.
Should not have
• Should not have small print or lots of text. Both sides need to capture attention.

```html
<!DOCTYPE html>
<html lang="en">
<head>
<meta charset="utf-8">
<title>Pellworth Fiber Optic Internet Postcard</title>
<link rel="stylesheet" href="https://fonts.googleapis.com/css2?family=Bebas+Neue&family=Montserrat:wght@500;600;700&display=swap">
<style>
  :root {
    --backdrop: #d4cdc2;
    --paper: #ffffff;
    --brand-blue: #0a74c6;
    --bright-blue: #0a96da;
    --price-shadow: #0672b0;
    --ink: #111111;
    --white: #ffffff;
    --faint: #d9d9d9;
  }
  * { box-sizing: border-box; margin: 0; padding: 0; }
  html, body { width: 921px; height: 1200px; overflow: hidden; }
  body { background: var(--backdrop); position: relative; font-family: "Montserrat", sans-serif; }

  .postcard { position: absolute; left: 80px; width: 760px; height: 506px; background: var(--paper); overflow: hidden; }
  .postcard--front { top: 76px; }
  .postcard--back { top: 618px; }

  .panel-shape { position: absolute; left: 0; top: 0; }

  .brand { position: absolute; left: 30px; top: 31px; display: flex; align-items: center; gap: 12px; }
  .brand__dot { width: 66px; height: 66px; border-radius: 50%; background: var(--brand-blue); }
  .brand__name { font-weight: 600; font-size: 20px; color: var(--white); margin-top: 26px; }

  .headline { position: absolute; left: 33px; font-family: "Bebas Neue", sans-serif; font-weight: 400; font-size: 84px; line-height: 1; letter-spacing: 0.5px; text-shadow: 0 4px 10px rgba(0,0,0,0.4); white-space: nowrap; }
  .headline--top { top: 156px; color: var(--white); }
  .headline--bottom { top: 235px; color: var(--brand-blue); }

  .referral { position: absolute; left: 36px; top: 362px; width: 326px; border-left: 3px solid var(--brand-blue); padding-left: 10px; }
  .referral__slogan { font-weight: 700; font-size: 16.5px; color: var(--brand-blue); text-transform: uppercase; line-height: 1; margin-bottom: 9px; white-space: nowrap; }
  .referral__body { font-weight: 500; font-size: 12.2px; line-height: 17.6px; letter-spacing: 0.3px; color: var(--white); text-align: justify; }

  .speed-bubble { position: absolute; left: 496px; top: 30px; }
  .speed-bubble__text { position: absolute; left: 506px; top: 48px; width: 190px; font-family: "Bebas Neue", sans-serif; font-size: 24px; line-height: 29px; color: var(--white); text-align: center; white-space: nowrap; transform: rotate(-4deg); }

  .price { position: absolute; left: 464px; top: 189px; font-family: "Bebas Neue", sans-serif; font-size: 215px; line-height: 1; color: var(--bright-blue); letter-spacing: -2px; text-shadow: 3px 4px 0 var(--price-shadow); white-space: nowrap; }

  .phone { position: absolute; right: 30px; top: 404px; font-family: "Bebas Neue", sans-serif; font-size: 54px; line-height: 1; color: var(--brand-blue); white-space: nowrap; }
  .web { position: absolute; right: 30px; top: 454px; font-weight: 700; font-size: 17px; line-height: 1.2; color: var(--ink); white-space: nowrap; }

  .cable-photo { position: absolute; left: 456px; top: 0; width: 304px; height: 281px; background: radial-gradient(ellipse at 50% 50%, #8fb9c9 0%, #d7e6ec 45%, #ffffff 75%); }

  .best-for { position: absolute; left: 33px; top: 121px; font-family: "Bebas Neue", sans-serif; font-weight: 400; font-size: 45px; line-height: 1; color: var(--brand-blue); text-shadow: 0 3px 8px rgba(0,0,0,0.4); white-space: nowrap; }
  .uses { position: absolute; left: 33px; top: 166px; list-style: none; }
  .uses__item { font-weight: 700; font-size: 28px; line-height: 38px; color: var(--white); }

  .mailing-area { position: absolute; left: 0; top: 396px; width: 760px; text-align: center; font-size: 12px; letter-spacing: 19px; color: var(--faint); font-weight: 500; }
</style>
</head>
<body>

<section class="postcard postcard--front">
  <svg class="panel-shape" width="760" height="506" viewBox="0 0 760 506" aria-hidden="true">
    <defs>
      <linearGradient id="navy-front" x1="0" y1="0" x2="1" y2="1">
        <stop offset="0" stop-color="#0b1535"/>
        <stop offset="0.55" stop-color="#0f2e5c"/>
        <stop offset="1" stop-color="#10497f"/>
      </linearGradient>
      <filter id="edge-shadow-front" x="-10%" y="-10%" width="130%" height="130%">
        <feDropShadow dx="6" dy="0" stdDeviation="8" flood-color="#000" flood-opacity="0.3"/>
      </filter>
    </defs>
    <path d="M0 0 H461 C392 90 372 220 381 300 C390 390 420 460 454 506 H0 Z" fill="url(#navy-front)" filter="url(#edge-shadow-front)"/>
  </svg>

  <div class="brand">
    <span class="brand__dot"></span>
    <span class="brand__name">Pellworth</span>
  </div>

  <h1 class="headline headline--top">Fiber Optic</h1>
  <h1 class="headline headline--bottom">Internet</h1>

  <div class="referral">
    <p class="referral__slogan">I Got Zoomed with Pellworth</p>
    <p class="referral__body">Existing customers can earn a $50 credit for every new customer they refer to us. Unlike most large cable and internet companies we have very happy customers... some who have stayed with us for decades.</p>
  </div>

  <svg class="speed-bubble" width="210" height="156" viewBox="0 0 210 156" aria-hidden="true">
    <path d="M34 6 L180 0 L196 14 L186 94 L104 116 L50 150 L66 114 L18 110 L4 58 Z" fill="#0a6fbf"/>
    <path d="M38 12 L176 6 L190 18 L180 88 L102 110 L60 138 L72 108 L22 104 L10 58 Z" fill="#0a8ad4"/>
  </svg>
  <p class="speed-bubble__text">Speeds up to<br>1 Gig with packages<br>starting at</p>

  <p class="price">$55</p>
  <p class="phone">555-318-2094</p>
  <p class="web">www.brightmesh.example</p>
</section>

<section class="postcard postcard--back">
  <svg class="panel-shape" width="760" height="296" viewBox="0 0 760 296" aria-hidden="true">
    <defs>
      <linearGradient id="navy-back" x1="0" y1="0" x2="1" y2="1">
        <stop offset="0" stop-color="#0b1535"/>
        <stop offset="0.55" stop-color="#0f2e5c"/>
        <stop offset="1" stop-color="#10497f"/>
      </linearGradient>
      <filter id="edge-shadow-back" x="-10%" y="-10%" width="130%" height="130%">
        <feDropShadow dx="6" dy="0" stdDeviation="8" flood-color="#000" flood-opacity="0.3"/>
      </filter>
    </defs>
    <path d="M0 0 H461 C400 80 378 190 382 296 H0 Z" fill="url(#navy-back)" filter="url(#edge-shadow-back)"/>
  </svg>

  <div class="cable-photo" role="img" aria-label="Photo of a cut fiber optic cable showing colourful inner tubes and glass strands"></div>

  <div class="brand">
    <span class="brand__dot"></span>
    <span class="brand__name">Pellworth</span>
  </div>

  <h2 class="best-for">Fiber is the best for:</h2>
  <ul class="uses">
    <li class="uses__item">Streaming</li>
    <li class="uses__item">Gaming</li>
    <li class="uses__item">Reliability</li>
  </ul>

  <p class="mailing-area">MAILING ADDRESS</p>
</section>

</body>
</html>
```